hello! I need a very simple modern business card for a new venture called The Quiet Harbour Retreats. It's the very first Tech-Free retreat in Asia!

The concept is very unique. Basically a group of 12-15 people would go on a 3 to 4 days retreat where no phone or internet is allowed. The first retreat will take place in a beautiful villa in Bali by the sea. It will include yoga, meditation, art & writing workshops, swimming, hiking, cooking, healthy vegetarian meals, etc.

Reason: Thanks for your submissions. I still haven't found exactly what I'm after but the designs that haven't be eliminated are getting close.. Please keep in mind that it should be a simple, modern and upmarket business card. Thanks

Target Market(s)

Both men and women who would like to disconnect from life, computer and phone for 3/4 days. They can be either local or expats but based in Asia (Singapore, Hong Kong).
Client will have to pay for their own flight and then the price is around US$600 for a 3-day retreat including everything (accommodation, food, activities). It means clients already have a good income. They are usually working in marketing, advertising, digital media, public relations.

Industry/Entity Type

Internet

Font styles to use
Other font styles liked:
• anything modern you like

Colors
acd036
9bcb3c
f37022
f68d4d
1b1b1b
333333
acd037

Requirements
Must have
• Name: Rell Vonta
Position: #screenwanderer
Company: The Quiet Harbour Retreats (asia should be smaller than the rest)
- Email button - quietharbourretreats@mailora.com
- Pagenook button - www.pagenook.com/quietharbourretreats
- Ticketvale button - www.quietharbourretreats.ticketvale.com
Nice to have
• You can use my logo attached but it's something I designed quickly on Power Point so it would be nice to include your own version.
Should not have
• anything tacky or girly or childish. thanks

```html
<!DOCTYPE html>
<html lang="en">
<head>
<meta charset="utf-8">
<title>The Quiet Harbour Retreats – Business Card</title>
<link rel="stylesheet" href="https://fonts.googleapis.com/css2?family=Marcellus&display=swap">
<style>
  :root {
    --leaf-green: #acd036;
    --orange: #f68d4d;
    --ink: #1b1b1b;
    --text: #333333;
    --page: #ffffff;
    --card: #ffffff;
    --link-blue: #3a66ad;
    --tag-orange: #f37022;
  }
  html, body {
    margin: 0;
    padding: 0;
    width: 1200px;
    height: 1000px;
    overflow: hidden;
    background: var(--page);
  }
  body {
    position: relative;
    font-family: "Marcellus", serif;
    color: var(--text);
  }
  .card {
    position: absolute;
    left: 303px;
    width: 609px;
    height: 351px;
    background: var(--card);
    box-shadow: 0 2px 4px rgba(0,0,0,0.35);
    border-top: 1px solid #eeeeee;
    overflow: hidden;
  }
  .card--front { top: 94px; }
  .card--back { top: 504px; }

  .rule {
    position: absolute;
    height: 2px;
    background: var(--leaf-green);
  }
  .brand-dot {
    position: absolute;
    border-radius: 50%;
    background: var(--leaf-green);
  }
  .brand-name {
    position: absolute;
    margin: 0;
    font-weight: 400;
    color: var(--ink);
    white-space: nowrap;
    line-height: 1;
  }

  /* front */
  .card--front .rule--left { left: 0; top: 258px; width: 82px; }
  .card--front .rule--right { left: 137px; top: 258px; width: 472px; }
  .card--front .brand-dot { left: 96px; top: 245px; width: 28px; height: 28px; }
  .card--front .brand-name { left: 184px; top: 221px; font-size: 25px; }

  /* back */
  .card--back .rule--left { left: 0; top: 167px; width: 29px; }
  .card--back .rule--right { left: 82px; top: 167px; width: 527px; }
  .card--back .brand-dot { left: 42px; top: 155px; width: 26px; height: 26px; }
  .card--back .brand-name { left: 115px; top: 136px; font-size: 21px; }

  .person {
    position: absolute;
    right: 28px;
    top: 96px;
    text-align: right;
    line-height: 1;
  }
  .person__name {
    margin: 0;
    font-size: 37px;
    font-weight: 400;
    color: var(--ink);
    letter-spacing: 0.5px;
  }
  .person__role {
    margin: 6px 0 0;
    font-size: 23px;
    color: var(--orange);
  }

  .contacts {
    position: absolute;
    right: 32px;
    top: 210px;
    margin: 0;
    padding: 0;
    list-style: none;
  }
  .contacts li {
    display: flex;
    justify-content: flex-end;
    align-items: center;
    height: 34px;
    font-size: 19px;
    color: var(--ink);
  }
  .contacts .icon {
    margin-left: 12px;
    width: 32px;
    display: flex;
    justify-content: center;
  }
  .square {
    display: block;
    width: 28px;
    height: 28px;
    border-radius: 4px;
  }
  .square--pagenook { background: var(--link-blue); }
  .square--ticketvale { background: var(--tag-orange); }
</style>
</head>
<body>

<section class="card card--front" aria-label="Card front">
  <div class="rule rule--left"></div>
  <div class="brand-dot"></div>
  <div class="rule rule--right"></div>
  <h1 class="brand-name">The Quiet Harbour Retreats</h1>
</section>

<section class="card card--back" aria-label="Card back">
  <div class="rule rule--left"></div>
  <div class="brand-dot"></div>
  <div class="rule rule--right"></div>
  <h2 class="brand-name">The Quiet Harbour Retreats</h2>

  <div class="person">
    <p class="person__name">Rell Vonta</p>
    <p class="person__role">#screenwanderer</p>
  </div>

  <ul class="contacts">
    <li>
      <span>quietharbourretreats@mailora.com</span>
      <span class="icon">
        <svg width="32" height="22" viewBox="0 0 32 22" aria-hidden="true">
          <rect x="0" y="0" width="32" height="22" fill="#acd036"/>
          <polyline points="1,1 16,12 31,1" fill="none" stroke="#ffffff" stroke-width="1.6"/>
          <polyline points="1,21 12,10" fill="none" stroke="#ffffff" stroke-width="1.6"/>
          <polyline points="31,21 20,10" fill="none" stroke="#ffffff" stroke-width="1.6"/>
        </svg>
      </span>
    </li>
    <li>
      <span>www.pagenook.com/quietharbourretreats</span>
      <span class="icon"><span class="square square--pagenook"></span></span>
    </li>
    <li>
      <span>www.quietharbourretreats.ticketvale.com</span>
      <span class="icon"><span class="square square--ticketvale"></span></span>
    </li>
  </ul>
</section>

</body>
</html>
```